Business Card Design

We need a business card designed for our new company. Prefer a black card with white logo & writing.

Contact Information for Business Card

Ted Galloway, address: 7-4812 Fernhollow Road, Abbotsford, BC, V3K 8R2, Office Phone: 604-712-3390, Cell: 604-947-2164, Email: ted@resinworkshub.ca

Colors

Designer to choose only greyscale colors for use in the design.

```html
<!DOCTYPE html>
<html lang="en">
<head>
<meta charset="utf-8">
<title>Resinworks Hub – Business Card</title>
<link href="https://fonts.googleapis.com/css2?family=Montserrat:wght@300;400&display=swap" rel="stylesheet">
<style>
  :root {
    --backdrop: #262626;
    --card: #000000;
    --ink: #ffffff;
  }
  * { margin: 0; padding: 0; box-sizing: border-box; }
  html, body {
    width: 1200px;
    height: 900px;
    overflow: hidden;
    background: var(--backdrop);
    font-family: "Montserrat", sans-serif;
    color: var(--ink);
  }
  .card {
    position: absolute;
    left: 341px;
    width: 518px;
    height: 296px;
    background: var(--card);
  }
  .card-front { top: 141px; }
  .card-back  { top: 463px; }

  .holder-name {
    position: absolute;
    right: 278px;
    top: 126px;
    font-weight: 300;
    font-size: 23px;
    letter-spacing: 2px;
    white-space: nowrap;
    text-transform: uppercase;
  }
  .divider {
    position: absolute;
    left: 259px;
    top: 80px;
    width: 1.5px;
    height: 135px;
    background: var(--ink);
  }
  .contact-list {
    position: absolute;
    left: 280px;
    top: 76px;
    list-style: none;
  }
  .contact-item {
    display: flex;
    align-items: center;
    height: 36px;
    margin-bottom: 17.5px;
  }
  .contact-icon {
    width: 25px;
    height: 27px;
    flex: none;
    margin-right: 8px;
  }
  .contact-text {
    font-weight: 400;
    font-size: 13.2px;
    line-height: 18px;
    white-space: nowrap;
  }
  .contact-text .label { margin-left: 6px; }

  .brand-name {
    position: absolute;
    inset: 0;
    display: flex;
    align-items: center;
    justify-content: center;
    font-weight: 400;
    font-size: 30px;
    letter-spacing: 4px;
    text-transform: uppercase;
  }
</style>
</head>
<body>

<section class="card card-front">
  <h1 class="holder-name">Ted Galloway</h1>
  <div class="divider"></div>
  <ul class="contact-list">
    <li class="contact-item">
      <svg class="contact-icon" viewBox="0 0 25 27" aria-hidden="true">
        <polygon points="12.5,0 25,6.75 25,20.25 12.5,27 0,20.25 0,6.75" fill="#fff"/>
        <path d="M12.5 5.5a5.5 5.5 0 0 0-5.5 5.5c0 4.2 5.5 10 5.5 10s5.5-5.8 5.5-10a5.5 5.5 0 0 0-5.5-5.5z" fill="#000"/>
        <circle cx="12.5" cy="11" r="2.2" fill="#fff"/>
      </svg>
      <p class="contact-text">7-4812 Fernhollow Road<br>Abbotsford, BC, V3K 8R2</p>
    </li>
    <li class="contact-item">
      <svg class="contact-icon" viewBox="0 0 25 27" aria-hidden="true">
        <polygon points="12.5,0 25,6.75 25,20.25 12.5,27 0,20.25 0,6.75" fill="#fff"/>
        <path d="M8.2 6.5l2.6-.6 1.4 3.6-1.7 1.3c.8 1.9 2.1 3.3 3.8 4.2l1.4-1.6 3.5 1.5-.6 2.6c-.2.7-.8 1.1-1.5 1.1-5.3-.5-9.4-4.7-9.9-10-.1-.7.3-1.3 1-1.5z" fill="#000"/>
      </svg>
      <p class="contact-text">604-712-3390<br>604-947-2164<span class="label">Cell</span></p>
    </li>
    <li class="contact-item">
      <svg class="contact-icon" viewBox="0 0 25 27" aria-hidden="true">
        <polygon points="12.5,0 25,6.75 25,20.25 12.5,27 0,20.25 0,6.75" fill="#fff"/>
        <rect x="6.5" y="9" width="12" height="9" rx="1" fill="#000"/>
        <polyline points="7.3,10 12.5,14 17.7,10" fill="none" stroke="#fff" stroke-width="1.2"/>
      </svg>
      <p class="contact-text">ted@resinworkshub.ca<br>www.resinworkshub.ca</p>
    </li>
  </ul>
</section>

<section class="card card-back">
  <p class="brand-name">Resinworks Hub</p>
</section>

</body>
</html>
```